Business card design

Hi,
I need to have a business card design based on the current logo.
If competitive I not put it out to everyone.

It can be single of double sided

Target Market(s)

Food businesses

Industry/Entity Type

Food Manufacturing

Contact Information for Business Card

Details will on card will be as follows Name = Marcus Bell Email = Marcus@PanHearth.com.au Phone = 0418563207 Address = 57 Larkin Street , Fortitude Valley QLD 4006 Australia

Font styles to use
Other font styles liked:
• based on two fonts - Adelle & Museo

Requirements
Must have
• Based on the on switch concept

```html
<!DOCTYPE html>
<html lang="en">
<head>
<meta charset="utf-8">
<title>PanHearth Business Card</title>
<link rel="stylesheet" href="https://fonts.googleapis.com/css2?family=Arimo:wght@400;700&family=Zilla+Slab:wght@500&display=swap">
<style>
  :root {
    --backdrop: #e3e3e3;
    --brand-red: #e8264a;
    --brand-red-deep: #c4253f;
    --brand-dark: #3b2a2c;
    --ink: #2e2426;
    --paper: #ffffff;
  }
  * { margin: 0; padding: 0; box-sizing: border-box; }
  html, body {
    width: 1200px;
    height: 900px;
    overflow: hidden;
    background: var(--backdrop);
    font-family: "Arimo", Arial, sans-serif;
  }
  .canvas { position: relative; width: 1200px; height: 900px; }

  .card {
    position: absolute;
    top: 217px;
    width: 309px;
    height: 500px;
  }

  /* Front side */
  .card--front {
    left: 279px;
    border-radius: 0 70px 0 70px;
    background: linear-gradient(30deg, var(--brand-dark) 8%, #7a2635 45%, var(--brand-red-deep) 70%, var(--brand-red) 100%);
    color: var(--paper);
  }
  .brand {
    position: absolute;
    display: flex;
    align-items: center;
    gap: 8px;
    font-family: "Arimo", Arial, sans-serif;
    font-weight: 700;
    letter-spacing: 0.5px;
    line-height: 1;
    white-space: nowrap;
  }
  .brand__dot {
    width: 26px;
    height: 26px;
    border-radius: 50%;
    flex: none;
  }
  .card--front .brand { left: 40px; top: 229px; font-size: 31px; color: var(--paper); }
  .card--front .brand__dot { background: var(--paper); }
  .tagline {
    position: absolute;
    right: 41px;
    top: 263px;
    font-family: "Zilla Slab", Georgia, serif;
    font-weight: 500;
    font-size: 11px;
    color: var(--paper);
    white-space: nowrap;
  }
  .front-url {
    position: absolute;
    left: 0;
    right: 0;
    top: 438px;
    text-align: center;
    font-size: 14px;
    color: var(--paper);
  }

  /* Back side */
  .card--back {
    left: 617px;
    border-radius: 70px 0 70px 0;
    background: var(--paper);
    color: var(--ink);
  }
  .card--back .brand { left: 27px; top: 117px; font-size: 33px; color: var(--ink); }
  .card--back .brand__dot { background: var(--brand-red); }

  .person-name {
    position: absolute;
    left: 33px;
    top: 265px;
    font-weight: 700;
    font-size: 20px;
    letter-spacing: 0.3px;
    color: var(--brand-red);
  }
  .address {
    position: absolute;
    left: 33px;
    top: 316px;
    font-style: normal;
    font-size: 14.5px;
    line-height: 18px;
  }
  .contact-list {
    position: absolute;
    left: 33px;
    top: 408px;
    list-style: none;
    font-size: 14.5px;
    line-height: 18px;
  }
  .contact-list li { display: flex; align-items: center; gap: 5px; white-space: nowrap; }
  .contact-icon { width: 13px; height: 13px; flex: none; }
</style>
</head>
<body>
<main class="canvas">

  <section class="card card--front" aria-label="Card front">
    <div class="brand"><span class="brand__dot"></span>PANHEARTH</div>
    <p class="tagline">Kitchen Supply Made Simple</p>
    <p class="front-url">www.PanHearth.com.au</p>
  </section>

  <section class="card card--back" aria-label="Card back">
    <div class="brand"><span class="brand__dot"></span>PANHEARTH</div>

    <h1 class="person-name">MARCUS BELL</h1>

    <address class="address">
      57 Larkin Street<br>
      Ashbury Vale<br>
      QLD 4087 Australia
    </address>

    <ul class="contact-list">
      <li>
        <svg class="contact-icon" viewBox="0 0 16 16" aria-hidden="true">
          <path d="M4 1.5l2.2 3-1.4 1.6c.8 1.8 2.2 3.3 4 4.2l1.6-1.4 3 2.2-1.3 2.6C7 13.5 2.5 9 1.4 2.8z" fill="none" stroke="#e8264a" stroke-width="1.6" stroke-linejoin="round"/>
          <path d="M9.5 1.8a5 5 0 0 1 4.7 4.7M9.3 4.3a2.5 2.5 0 0 1 2.4 2.4" fill="none" stroke="#e8264a" stroke-width="1.3" stroke-linecap="round"/>
        </svg>
        0418563207
      </li>
      <li>
        <svg class="contact-icon" viewBox="0 0 16 16" aria-hidden="true">
          <rect x="0.5" y="3" width="15" height="10" fill="#e8264a"/>
          <path d="M0.5 3.5L8 9l7.5-5.5" fill="none" stroke="#fff" stroke-width="1.3"/>
        </svg>
        Marcus@PanHearth.com.au
      </li>
      <li>
        <svg class="contact-icon" viewBox="0 0 16 16" aria-hidden="true">
          <g fill="none" stroke="#e8264a" stroke-width="1.3">
            <circle cx="8" cy="8" r="6.8"/>
            <ellipse cx="8" cy="8" rx="3" ry="6.8"/>
            <path d="M1.2 8h13.6M2.2 4.6h11.6M2.2 11.4h11.6"/>
          </g>
        </svg>
        www.PanHearth.com.au
      </li>
    </ul>
  </section>

</main>
</body>
</html>
```